Alberta, Canada based Environmental Oilfield Consultant need a Business Card Design

We need a business card design for a year old company based in Edmonton, Alberta, Canada called Cindermoor Consulting Inc. We are environmental consultants primarily for oilfield based companies (pipeline cleanup, site consultations, environmental site training, and site evaluations).

We like the color blue or green, something very clean and crisp looking.
We don't really care if there is an otter on it but most of our work is land based and nothing really to do with oceans or larger bodies of water.

The name Cindermoor was the name of our fathers boat, and named our company that in his memory.

```html
<!DOCTYPE html>
<html lang="en">
<head>
<meta charset="utf-8">
<title>Cindermoor Consulting Inc. – Business Card</title>
<link rel="stylesheet" href="https://fonts.googleapis.com/css2?family=Exo+2:wght@400;600;800&display=swap">
<style>
  :root {
    --backdrop: #e9e4dc;
    --card-white: #f7f7f7;
    --card-dark: #3b3b3d;
    --orange: #f29a1f;
    --yellow: #ffd21a;
    --grey-light: #c9c9c9;
    --grey-dark: #6f6f71;
    --ink: #4a4a4c;
    --white: #ffffff;
  }
  * { margin: 0; padding: 0; box-sizing: border-box; }
  html, body { width: 1071px; height: 1200px; overflow: hidden; }
  body {
    background: var(--backdrop);
    font-family: "Exo 2", sans-serif;
    position: relative;
  }
  .card {
    position: absolute;
    left: 105px;
    width: 860px;
    height: 491px;
    overflow: hidden;
    box-shadow: 0 14px 30px rgba(0,0,0,.22);
  }
  .card--front { top: 70px; background: var(--card-white); }
  .card--back { top: 635px; background: var(--card-dark); }
  .card svg.art { position: absolute; inset: 0; }

  .wordmark {
    position: absolute;
    font-weight: 800;
    color: var(--orange);
    line-height: .95;
    letter-spacing: 1px;
  }
  .card--front .wordmark { left: 48px; top: 92px; font-size: 66px; }
  .card--back .wordmark { left: 60px; top: 96px; font-size: 62px; }

  .person {
    position: absolute;
    right: 44px;
    top: 48px;
    text-align: right;
    color: var(--white);
  }
  .person__name { font-size: 40px; font-weight: 400; letter-spacing: 3px; }
  .person__title { font-size: 17px; font-weight: 600; letter-spacing: 3px; margin-top: 4px; }

  .address {
    position: absolute;
    left: 612px;
    top: 238px;
    display: flex;
    gap: 10px;
    color: var(--ink);
    font-size: 18px;
    line-height: 1.4;
    white-space: nowrap;
  }
  .address svg { flex: none; margin-top: 3px; }

  .contacts {
    position: absolute;
    left: 48px;
    top: 352px;
    list-style: none;
    color: var(--ink);
    font-size: 17px;
    line-height: 1.55;
  }
  .contacts li { display: flex; align-items: center; gap: 10px; }
  .contacts svg { flex: none; }

  .web {
    font-family: "Exo 2", sans-serif;
    font-size: 15px;
    font-weight: 600;
    letter-spacing: 1px;
    fill: var(--ink);
  }
</style>
</head>
<body>

<section class="card card--front" aria-label="Card front">
  <svg class="art" width="860" height="491" viewBox="0 0 860 491" aria-hidden="true">
    <defs>
      <linearGradient id="greyBand" x1="0" y1="0" x2="1" y2="0">
        <stop offset="0" stop-color="#e2e2e2"/>
        <stop offset=".45" stop-color="#9a9a9c"/>
        <stop offset="1" stop-color="#6f6f71"/>
      </linearGradient>
      <linearGradient id="sunPanel" x1="0" y1="1" x2="1" y2="0">
        <stop offset="0" stop-color="#f29a1f"/>
        <stop offset=".55" stop-color="#ffc21a"/>
        <stop offset="1" stop-color="#ffe14a"/>
      </linearGradient>
    </defs>
    <polygon class="band-grey" points="440,0 860,0 860,190 590,190 520,120" fill="url(#greyBand)"/>
    <polygon class="panel-sun" points="0,491 0,330 430,330 530,215 600,215 600,491" fill="url(#sunPanel)"/>
  </svg>

  <div class="wordmark">Cindermoor<br>Consulting</div>

  <div class="person">
    <div class="person__name">DANIEL REEVE</div>
    <div class="person__title">GENERAL MANAGER</div>
  </div>

  <div class="address">
    <svg width="14" height="20" viewBox="0 0 14 20"><path d="M7 0a7 7 0 0 0-7 7c0 5 7 13 7 13s7-8 7-13a7 7 0 0 0-7-7zm0 10a3 3 0 1 1 0-6 3 3 0 0 1 0 6z" fill="#3b3b3d"/></svg>
    <div>118 Elm Ridge Road, 3rd<br>building Street W.</div>
  </div>

  <ul class="contacts">
    <li><svg width="14" height="14" viewBox="0 0 14 14"><path d="M3 1l2 3-1.5 1.5a8 8 0 0 0 5 5L10 9l3 2-1 2.5C6 13 1 8 .5 2z" fill="#3b3b3d"/></svg>780 555 0142</li>
    <li><svg width="14" height="14" viewBox="0 0 14 14"><rect x="3" y="0" width="8" height="14" rx="1.5" fill="#3b3b3d"/><rect x="4.5" y="2" width="5" height="8" fill="#ffc21a"/></svg>780 555 0143</li>
    <li><svg width="14" height="14" viewBox="0 0 14 14"><rect x="1" y="5" width="12" height="7" fill="#3b3b3d"/><rect x="3" y="1" width="8" height="4" fill="#3b3b3d"/></svg>780 555 0144</li>
    <li><svg width="14" height="14" viewBox="0 0 14 14"><rect x="0" y="2" width="14" height="10" fill="#3b3b3d"/><path d="M0 2l7 5 7-5" stroke="#ffc21a" fill="none"/></svg>daniel@cindermoor.ca</li>
    <li><svg width="14" height="14" viewBox="0 0 14 14"><circle cx="7" cy="7" r="6.5" fill="#3b3b3d"/><path d="M.5 7h13M7 .5v13" stroke="#ffc21a"/></svg>www.cindermoor.ca</li>
  </ul>
</section>

<section class="card card--back" aria-label="Card back">
  <svg class="art" width="860" height="491" viewBox="0 0 860 491">
    <defs>
      <linearGradient id="sweep" x1="0" y1="0" x2="1" y2="0">
        <stop offset="0" stop-color="#6f6f71"/>
        <stop offset=".3" stop-color="#c9c9c9"/>
        <stop offset=".45" stop-color="#ffd21a"/>
        <stop offset=".6" stop-color="#d7d7d7"/>
        <stop offset="1" stop-color="#9a9a9c"/>
      </linearGradient>
    </defs>
    <polygon class="band-sweep" points="0,262 860,212 860,250 0,300" fill="url(#sweep)"/>
    <polygon class="line-orange" points="0,300 860,250 860,262 0,312" fill="#f29a1f"/>
    <polygon class="line-orange" points="0,250 860,200 860,206 0,256" fill="#f29a1f"/>
    <text class="web" x="650" y="249" transform="rotate(-3.33 650 249)">www.cindermoor.ca</text>
  </svg>

  <div class="wordmark">Cindermoor<br>Consulting</div>
</section>

</body>
</html>
```